Coastline Premier Retreats Business Card Design

Design a business card for Coastline Premier Retreats. Look at the website for colors and reference. Card should have logo, name, title, office number, mobile number, email, URL and a tagline like, "Luxury Hotel & Resort Email Marketing" (This might change).

https://www.coastlinepremierretreats.example

The rest I will leave up to your imagination.

Contact Information for Business Card

Logo, name, title, office number, mobile number, email, URL and a tagline like, "Luxury Hotel & Resort Email Marketing" (This might change).

```html
<!DOCTYPE html>
<html lang="en">
<head>
<meta charset="utf-8">
<title>Coastline Premier Retreats – Business Cards</title>
<link rel="stylesheet" href="https://fonts.googleapis.com/css2?family=Montserrat:ital,wght@0,400;0,700;1,500&display=swap">
<style>
  :root {
    --backdrop: #9a9a9a;
    --card: #1a1a1a;
    --accent: #f07a12;
    --ink: #ffffff;
    --muted-mark: #3b3b3b;
  }
  * { box-sizing: border-box; margin: 0; padding: 0; }
  html, body { width: 1200px; height: 854px; overflow: hidden; }
  body {
    background: var(--backdrop);
    font-family: "Montserrat", sans-serif;
    color: var(--ink);
    position: relative;
  }
  .card {
    position: absolute;
    width: 485px;
    height: 277px;
    background: var(--card);
    border-left: 3px solid var(--accent);
    border-bottom: 3px solid var(--accent);
    box-shadow: 8px 8px 14px rgba(0,0,0,0.28);
  }
  .card--a { left: 96px; top: 125px; }
  .card--b { left: 621px; top: 125px; }
  .card--c { left: 96px; top: 439px; }
  .card--back { left: 621px; top: 439px; }

  .brand {
    position: absolute;
    left: 27px;
    top: 54px;
    display: flex;
    align-items: center;
    gap: 8px;
  }
  .brand__square { width: 12px; height: 12px; background: var(--accent); }
  .brand__name {
    font-weight: 700;
    font-size: 15px;
    letter-spacing: 0.04em;
    line-height: 1.15;
    text-transform: uppercase;
    color: var(--ink);
  }

  .person {
    position: absolute;
    right: 24px;
    top: 120px;
    text-align: right;
  }
  .person__name {
    font-weight: 700;
    font-size: 21px;
    letter-spacing: 0.03em;
    color: var(--accent);
    text-transform: uppercase;
    line-height: 1.1;
  }
  .person__title { font-size: 11.5px; letter-spacing: 0.04em; line-height: 1.2; }
  .name-tab {
    position: absolute;
    right: 0;
    top: 126px;
    width: 13px;
    height: 28px;
    background: var(--accent);
  }

  .contacts {
    position: absolute;
    left: 27px;
    top: 177px;
    list-style: none;
    font-size: 11.5px;
    letter-spacing: 0.04em;
  }
  .contacts li {
    display: flex;
    align-items: center;
    gap: 6px;
    height: 18.5px;
  }
  .contacts svg { width: 9px; height: 9px; fill: var(--accent); flex: none; }
  .contacts .hl { color: var(--accent); }

  .back-mark {
    position: absolute;
    left: 0; right: 0;
    top: 112px;
    text-align: center;
    font-weight: 700;
    font-size: 26px;
    letter-spacing: 0.05em;
    color: var(--muted-mark);
    text-transform: uppercase;
  }
  .tagline {
    position: absolute;
    left: 0; right: 0;
    top: 228px;
    text-align: center;
    font-style: italic;
    font-weight: 500;
    font-size: 14px;
    color: var(--accent);
  }
</style>
</head>
<body>
<svg width="0" height="0" style="position:absolute">
  <defs>
    <symbol id="icon-mobile" viewBox="0 0 10 10"><path d="M3 0h4a1 1 0 0 1 1 1v8a1 1 0 0 1-1 1H3a1 1 0 0 1-1-1V1a1 1 0 0 1 1-1zm0 1.5v6h4v-6z"/></symbol>
    <symbol id="icon-phone" viewBox="0 0 10 10"><path d="M0 3.5C0 2 2 1.5 5 1.5S10 2 10 3.5V4.5H7.5V3.5h-5V4.5H0zM2 5h6l1 4H1z"/></symbol>
    <symbol id="icon-mail" viewBox="0 0 10 10"><path d="M0 4l5-3.5L10 4v6H0zm1 .6L5 7.5l4-2.9L5 1.8z"/></symbol>
    <symbol id="icon-web" viewBox="0 0 10 10"><path d="M5 0a5 5 0 1 1 0 10A5 5 0 0 1 5 0zM3 2.5L2 4l1.5 1.5L3 7.5 4.5 8 5 6 6.5 5 6 3.5 4.5 3zM7 1.8 6.5 3l1.5 1 .8-.6A4 4 0 0 0 7 1.8z"/></symbol>
  </defs>
</svg>

<article class="card card--a">
  <div class="brand"><span class="brand__square"></span><span class="brand__name">Coastline<br>Premier Retreats</span></div>
  <div class="person"><p class="person__name">Marcus Hale</p><p class="person__title">CEO/Founder</p></div>
  <span class="name-tab"></span>
  <ul class="contacts">
    <li><svg><use href="#icon-mobile"/></svg>555.014.2200</li>
    <li><svg><use href="#icon-phone"/></svg>+34 600 555 014</li>
    <li><svg><use href="#icon-mail"/></svg>marcus@coastlinepremierretreats.example</li>
    <li><svg><use href="#icon-web"/></svg>www.<span class="hl">coastlinepremierretreats</span>.example</li>
  </ul>
</article>

<article class="card card--b">
  <div class="brand"><span class="brand__square"></span><span class="brand__name">Coastline<br>Premier Retreats</span></div>
  <div class="person"><p class="person__name">Elena Voss</p><p class="person__title">CEO/Founder</p></div>
  <span class="name-tab"></span>
  <ul class="contacts">
    <li><svg><use href="#icon-mobile"/></svg>+34 600 555 014</li>
    <li><svg><use href="#icon-phone"/></svg>+123 555 01890</li>
    <li><svg><use href="#icon-mail"/></svg>elena@coastlinepremierretreats.example</li>
    <li><svg><use href="#icon-web"/></svg>www.<span class="hl">coastlinepremierretreats</span>.example</li>
  </ul>
</article>

<article class="card card--c">
  <div class="brand"><span class="brand__square"></span><span class="brand__name">Coastline<br>Premier Retreats</span></div>
  <div class="person"><p class="person__name">Dana Whitford</p><p class="person__title">CEO/Founder</p></div>
  <span class="name-tab"></span>
  <ul class="contacts">
    <li><svg><use href="#icon-mobile"/></svg>555.019.7344</li>
    <li><svg><use href="#icon-phone"/></svg>+123 555 01890</li>
    <li><svg><use href="#icon-mail"/></svg>dana@coastlinepremierretreats.example</li>
    <li><svg><use href="#icon-web"/></svg>www.<span class="hl">coastlinepremierretreats</span>.example</li>
  </ul>
</article>

<article class="card card--back">
  <p class="back-mark">Coastline Premier Retreats</p>
  <p class="tagline">Luxury Hotel &amp; Resort Email Marketing</p>
</article>
</body>
</html>
```